Elevating our current Business Card Design

We want to elevate our current business card with a new design to look like a zenith 300 company. We are a premium lubricant distributor (oil and grease).
We need 2 versions, version 1 is as per the uploaded a copy of our current business card with the English version.
For our Chinese version we need to use the front to be English in English and have the back of the card designed exactly like the front for all info to be in Chinese.
The design template needs to be such that we can amend the template with adding different information for each person's card.
The background colour of the card can be changed- we just need to clearly see all information on the card and logos.
The QJR and Ember steady logos cannot have any colour or display changes- only use the logos attached.
All logos need to be included and all information from the attached current card

```html
<!DOCTYPE html>
<html lang="en">
<head>
<meta charset="utf-8">
<title>KVL Business Card – Mara Castell</title>
<link rel="stylesheet" href="https://fonts.googleapis.com/css2?family=Ubuntu:wght@400;500;700&display=swap">
<style>
  :root {
    --stage: #232323;
    --card-dark: #29292d;
    --gold: #d39f2a;
    --gold-deep: #b8861c;
    --red: #e8262a;
    --white: #ffffff;
    --cert-orange: #ee7a1a;
    --muted: #cfcfcf;
  }
  * { box-sizing: border-box; margin: 0; padding: 0; }
  html, body { width: 1200px; height: 780px; overflow: hidden; }
  body {
    background: var(--stage);
    font-family: "Ubuntu", "Segoe UI", sans-serif;
    color: var(--white);
    display: flex;
    align-items: center;
    justify-content: center;
    gap: 70px;
  }
  .card {
    width: 340px;
    height: 600px;
    border-radius: 22px;
    position: relative;
    overflow: hidden;
    box-shadow: 0 18px 40px rgba(0,0,0,.55);
  }

  /* Front */
  .card-front { background: var(--gold); }
  .card-front .pattern {
    position: absolute; inset: 0;
    background: radial-gradient(circle at 50% 45%, var(--gold) 0%, var(--gold-deep) 100%);
  }
  .front-brand {
    position: absolute; inset: 0;
    display: flex; flex-direction: column; align-items: center; justify-content: center;
    gap: 34px;
  }
  .front-brand .brand-name {
    font-size: 118px; font-weight: 700; color: var(--red); letter-spacing: 2px;
  }
  .front-brand .brand-dot {
    width: 96px; height: 96px; border-radius: 50%; background: var(--white);
  }

  /* Back */
  .card-back {
    background: var(--card-dark);
    display: flex; flex-direction: column; align-items: center;
    padding: 44px 28px 26px;
    text-align: center;
  }
  .back-brand { display: flex; align-items: center; gap: 14px; }
  .back-brand .brand-dot { width: 30px; height: 30px; border-radius: 50%; background: var(--gold); }
  .back-brand .brand-name { font-size: 66px; font-weight: 700; color: var(--red); letter-spacing: 2px; }

  .person { margin-top: 42px; }
  .person-name { font-size: 34px; font-weight: 500; color: var(--red); line-height: 1; }
  .person-title { font-size: 15px; margin-top: 6px; }

  .divider {
    display: flex; align-items: center; gap: 8px; width: 100%; margin: 16px 0 12px;
  }
  .divider .rule { flex: 1; height: 2px; background: var(--red); }
  .icon {
    width: 24px; height: 24px; border-radius: 6px; background: var(--red);
    display: flex; align-items: center; justify-content: center;
  }
  .icon svg { width: 14px; height: 14px; }

  .contact-list { list-style: none; font-size: 15px; line-height: 1.55; }

  .address { font-size: 15px; line-height: 1.45; }

  .badges {
    margin-top: auto; width: 100%;
    display: flex; flex-direction: column; align-items: flex-end; gap: 12px;
  }
  .cert-row { display: flex; gap: 12px; }
  .cert {
    width: 40px; height: 40px; border-radius: 50%;
    background: var(--cert-orange); border: 3px solid #9a9a9a;
  }
  .partner-row { display: flex; align-items: flex-end; gap: 10px; width: 100%; }
  .member-badge {
    width: 62px; height: 34px; border-radius: 18px 18px 4px 4px;
    border: 3px solid var(--white);
  }
  .distributor-box {
    flex: 1; display: flex; align-items: stretch;
    border: 2px solid var(--red); height: 40px;
  }
  .distributor-box .dist-name {
    flex: 1; display: flex; align-items: center; justify-content: center;
    font-size: 20px; font-weight: 700; color: var(--red);
  }
  .distributor-box .partner-mark { width: 92px; background: var(--red); }
</style>
</head>
<body>

  <section class="card card-front" aria-label="Card front">
    <div class="pattern" role="img" aria-label="Repeating gold dotted brand motif pattern"></div>
    <div class="front-brand">
      <span class="brand-name">KVL</span>
      <span class="brand-dot"></span>
    </div>
  </section>

  <section class="card card-back" aria-label="Card back">
    <div class="back-brand">
      <span class="brand-dot"></span>
      <span class="brand-name">KVL</span>
    </div>

    <div class="person">
      <h1 class="person-name">Mara Castell</h1>
      <p class="person-title">Administration Executive</p>
    </div>

    <div class="divider">
      <span class="rule"></span>
      <span class="icon"><svg viewBox="0 0 16 16"><path d="M4 1l3 3-2 2c1 2 3 4 5 5l2-2 3 3-2 2C7 14 2 9 2 3z" fill="#fff"/></svg></span>
      <span class="icon"><svg viewBox="0 0 16 16"><rect x="2" y="5" width="12" height="9" rx="1" fill="#fff"/><rect x="4" y="2" width="8" height="4" fill="#fff"/></svg></span>
      <span class="icon"><svg viewBox="0 0 16 16"><rect x="1" y="3" width="14" height="10" rx="1" fill="#fff"/><path d="M1 4l7 5 7-5" stroke="#e8262a" stroke-width="1.5" fill="none"/></svg></span>
      <span class="icon"><svg viewBox="0 0 16 16"><circle cx="8" cy="8" r="6.5" fill="none" stroke="#fff" stroke-width="1.6"/><path d="M1.5 8h13M8 1.5c-3 3-3 10 0 13M8 1.5c3 3 3 10 0 13" stroke="#fff" stroke-width="1.2" fill="none"/></svg></span>
      <span class="rule"></span>
    </div>

    <ul class="contact-list">
      <li>1300 555 204 (Phone)</li>
      <li>+61 400 555 318 (Mobaill)</li>
      <li>+61 8 5550 1942 (Fax)</li>
      <li>mara.castell@kvldirect.com</li>
      <li>www.kvldirect.com</li>
    </ul>

    <div class="divider">
      <span class="rule"></span>
      <span class="icon"><svg viewBox="0 0 16 16"><path d="M8 1a5 5 0 0 0-5 5c0 4 5 9 5 9s5-5 5-9a5 5 0 0 0-5-5z" fill="#fff"/><circle cx="8" cy="6" r="2" fill="#e8262a"/></svg></span>
      <span class="rule"></span>
    </div>

    <p class="address">48 Freightway Drive<br>Harlow, WA 6199</p>

    <div class="badges">
      <div class="cert-row">
        <span class="cert"></span><span class="cert"></span><span class="cert"></span>
      </div>
      <div class="partner-row">
        <span class="member-badge"></span>
        <div class="distributor-box">
          <span class="dist-name">KVL</span>
          <span class="partner-mark"></span>
        </div>
      </div>
    </div>
  </section>

</body>
</html>
```